Signage Design Project - For Sale and For Rent

I am looking to revamp our For Sale and For Rent signboards.
The size of the board is
1250mm WIDTH
1800mm HEIGHT
The board is one sided, and slightly curved (will not impact the design at all)
For Rent Signs need to include the following information;
NESTor Logo
For Rent
Website
Facebook link (www.nestbook.example/nestorhomesco)
Phone number 6148 7309
For Sale signs need to include the following information
NESTor logo
For Sale
Website
Facebook link
Phone number 6148 7309
One signboard with Colin Partridge (this is the agents name)
One signboard with Peter Halvey (this is the agents name)
Full service real estate for a low $5,950 (+GST)
The more bold, punch and creative the better- we are very much an innovative and young company. I would suggest visiting our website, www.nestorhomes.example.au and our facebook page to get a feel for our company.
Updates
Existing signboard + logo files have been updated.
Have also guaranteed payment.
Real Estate

```html
<!DOCTYPE html>
<html lang="en">
<head>
<meta charset="utf-8">
<title>NESTor Property – For Sale Signboard</title>
<link rel="stylesheet" href="https://fonts.googleapis.com/css2?family=League+Gothic&family=Montserrat:wght@600;700&display=swap">
<style>
  :root {
    --page: #f2f2f0;
    --board: #e4eedd;
    --skyline: #a9c59b;
    --brand-green: #5f9a4e;
    --url-green: #6a9c55;
    --badge: #9dbd8b;
    --ink: #111111;
    --paper: #ffffff;
  }
  html, body {
    margin: 0;
    width: 1026px;
    height: 1200px;
    overflow: hidden;
    background: var(--page);
  }
  .signboard {
    position: absolute;
    left: 96px;
    top: 0;
    width: 833px;
    height: 1200px;
  }
  .signboard svg { display: block; }
  .display { font-family: "League Gothic", "Oswald", sans-serif; }
  .sans { font-family: "Montserrat", "Helvetica Neue", Arial, sans-serif; font-weight: 700; }
</style>
</head>
<body>
  <main class="signboard">
    <svg width="833" height="1200" viewBox="0 0 833 1200" aria-labelledby="sign-title">
      <title id="sign-title">NESTor Property – For Sale</title>

      <rect class="board-bg" width="833" height="1200" fill="var(--board)"/>

      <rect class="skyline" x="0" y="660" width="833" height="540" fill="var(--skyline)"
            role="img" aria-label="Rooftop skyline silhouette of houses and chimneys"/>

      <g class="brand">
        <rect class="brand-square" x="94" y="58" width="58" height="58" fill="var(--brand-green)"/>
        <text class="brand-name sans" x="172" y="106" font-size="50" fill="var(--ink)">NESTor</text>
      </g>

      <g class="headline display" fill="var(--ink)">
        <rect class="rule" x="259" y="179" width="311" height="15"/>
        <text x="259" y="507" font-size="405" textLength="311" lengthAdjust="spacingAndGlyphs">FOR</text>
        <text x="259" y="737" font-size="295" textLength="311" lengthAdjust="spacingAndGlyphs">SALE</text>
        <rect class="rule" x="259" y="746" width="311" height="14"/>
      </g>

      <g class="price-badge display" fill="var(--paper)" text-anchor="middle">
        <circle cx="644" cy="500" r="88" fill="var(--badge)"/>
        <text x="644" y="464" font-size="32">FULL SERVICE</text>
        <text x="644" y="494" font-size="32">REAL ESTATE</text>
        <line x1="596" y1="505" x2="612" y2="505" stroke="var(--paper)" stroke-width="2"/>
        <text x="644" y="511" font-size="15">FOR A LOW</text>
        <line x1="676" y1="505" x2="692" y2="505" stroke="var(--paper)" stroke-width="2"/>
        <text x="638" y="562" font-size="56">$5,950</text>
        <text x="699" y="532" font-size="13" text-anchor="start">+GST</text>
      </g>

      <g class="contact display">
        <text class="agent-name" x="259" y="860" font-size="105" textLength="311" lengthAdjust="spacingAndGlyphs"><tspan fill="var(--ink)">PETER</tspan><tspan fill="var(--paper)">HALVEY</tspan></text>
        <text class="phone" x="259" y="965" font-size="127" fill="var(--paper)" textLength="311" lengthAdjust="spacingAndGlyphs">6148-7309</text>
        <rect class="rule" x="259" y="977" width="311" height="13" fill="var(--paper)"/>
        <text class="website" x="259" y="1070" font-size="66" fill="var(--url-green)" textLength="311" lengthAdjust="spacingAndGlyphs">NESTORHOMES.EXAMPLE.AU</text>
        <rect class="rule" x="259" y="1091" width="311" height="17" fill="var(--paper)"/>
      </g>

      <g class="social">
        <rect class="social-square" x="128" y="1124" width="46" height="46" rx="3" fill="var(--brand-green)"/>
        <text class="sans" x="203" y="1157" font-size="24" fill="var(--paper)" textLength="494" lengthAdjust="spacingAndGlyphs">WWW.NESTBOOK.EXAMPLE/NESTORHOMESCO</text>
      </g>
    </svg>
  </main>
</body>
</html>
```